Asphalt Driveway Billboard Design

We need a billboard designed for an Asphalt & Concrete Company in Minnesota. We want to advertise Asphalt Driveways on this billboard! Logo is uploaded below. Our website is pinecrest-paving.com for more information.

```html
<!DOCTYPE html>
<html lang="en">
<head>
<meta charset="utf-8">
<title>Pinecrest Paving Billboard</title>
<link rel="stylesheet" href="https://fonts.googleapis.com/css2?family=Roboto:wght@500;700&family=Roboto+Condensed:ital,wght@1,700&display=swap">
<style>
  :root {
    --page: #b4b4b4;
    --ink: #141213;
    --paper: #ffffff;
    --blue-deep: #0a4b96;
    --blue-bright: #1ea4da;
    --silver: #a7a7a9;
  }
  html, body {
    margin: 0;
    width: 1200px;
    height: 1200px;
    overflow: hidden;
    background: var(--page);
  }
  .billboard {
    position: absolute;
    left: 40px;
    top: 320px;
    width: 1120px;
    height: 560px;
    display: block;
    box-shadow: 0 6px 18px rgba(0,0,0,0.25);
  }
  .brand-name {
    font-family: "Roboto", sans-serif;
    font-weight: 700;
    font-size: 84px;
    fill: var(--ink);
  }
  .contact {
    font-family: "Roboto", sans-serif;
    font-weight: 700;
    font-size: 36px;
    fill: var(--ink);
  }
  .service {
    font-family: "Roboto", sans-serif;
    font-weight: 500;
    font-size: 62px;
    fill: var(--paper);
  }
  .service-dot { fill: var(--blue-deep); }
  .tagline {
    font-family: "Roboto Condensed", sans-serif;
    font-style: italic;
    font-weight: 700;
    font-size: 38px;
    fill: var(--paper);
  }
</style>
</head>
<body>
<svg class="billboard" viewBox="0 0 1692 845" xmlns="http://www.w3.org/2000/svg">
  <defs>
    <linearGradient id="swoosh-blue" x1="0.9" y1="0" x2="0.4" y2="1">
      <stop offset="0" stop-color="var(--blue-bright)"/>
      <stop offset="0.6" stop-color="var(--blue-deep)"/>
    </linearGradient>
    <linearGradient id="band-blue" x1="0" y1="0" x2="1" y2="0">
      <stop offset="0" stop-color="var(--blue-deep)"/>
      <stop offset="0.6" stop-color="#0b62ad"/>
      <stop offset="1" stop-color="var(--blue-bright)"/>
    </linearGradient>
  </defs>

  <rect class="board-bg" width="1692" height="845" fill="var(--ink)"/>

  <path class="swoosh-blue" d="M700 0 L960 0 C1010 200 980 560 420 845 L0 845 L0 0 Z" fill="url(#swoosh-blue)"/>
  <path class="panel-white" d="M0 0 L700 0 C860 170 880 560 420 845 L0 845 Z" fill="var(--paper)"/>
  <path class="swoosh-silver" d="M0 632 C200 760 520 770 710 600 C560 760 300 860 0 785 Z" fill="var(--silver)"/>

  <g class="brand">
    <circle cx="395" cy="230" r="110" fill="var(--blue-deep)"/>
    <text class="brand-name" x="395" y="480" text-anchor="middle">Pinecrest Paving</text>
    <text class="contact" x="385" y="607" text-anchor="middle">www.pinecrest-paving.com</text>
    <text class="contact" x="385" y="652" text-anchor="middle">612.555.0148</text>
  </g>

  <g class="services">
    <text class="service" x="1607" y="172" text-anchor="end">Asphalt Driveways</text>
    <circle class="service-dot" cx="1632" cy="155" r="7"/>
    <text class="service" x="1607" y="277" text-anchor="end">Concrete Driveways</text>
    <circle class="service-dot" cx="1632" cy="260" r="7"/>
    <text class="service" x="1607" y="382" text-anchor="end">Concrete Aprons</text>
    <circle class="service-dot" cx="1632" cy="365" r="7"/>
    <text class="service" x="1607" y="487" text-anchor="end">Sidewalks &amp; Patios</text>
    <circle class="service-dot" cx="1632" cy="470" r="7"/>
    <text class="service" x="1607" y="592" text-anchor="end">Sealcoating</text>
    <circle class="service-dot" cx="1632" cy="577" r="7"/>
  </g>

  <polygon class="tagline-band" points="842,651 1692,651 1692,739 762,739" fill="url(#band-blue)"/>
  <text class="tagline" x="1640" y="708" text-anchor="end">PAVING THE WAY WITH CONCRETE RESULTS!</text>
</svg>
</body>
</html>
```